Luxury Business Card Design for High-End Window Treatments

Gilded Slatworks
Custom Plantation Shutters & Architectural Shading Systems

⸻

BACK

Daniel Trevick
Owner

Custom Interior & Exterior Window Treatments

919-555-0148
gildedslatworks.com

I have included a picture that I’m hoping we can use on the back, but I’m also wondering if you can get rid of the ladder? Should we get rid of shutters , shades and blinds underneath Gilded Slatworks?

Target Market(s)

High-end residential homeowners, custom home builders, architects, interior designers, and luxury renovation clients seeking premium plantation shutters and motorized architectural shading systems.

Industry/Entity Type

Custom Window treatments

Contact Information for Business Card

Front Gilded Slatworks Custom Plantation Shutters Motorized Architectural Shading Systems BACK Daniel Trevick Owner 919-555-0148 GildedSlatworks.com Custom Interior & Exterior Window Treatments By Appointment

Requirements
Nice to have
• Not 100% sure on nice to halves or the color but you can definitely check out my website to get a better understanding of what I’m trying to do

```html
<!DOCTYPE html>
<html lang="en">
<head>
<meta charset="utf-8">
<title>Gilded Slatworks – Business Card</title>
<link href="https://fonts.googleapis.com/css2?family=Open+Sans:wght@400;600;700&family=Cormorant+Garamond:wght@700&display=swap" rel="stylesheet">
<style>
  :root {
    --bg: #e9e8e6;
    --card-black: #1c1c1c;
    --gold: #f2c94c;
    --gold-edge: #c9a43a;
    --ivory: #eceae3;
    --sky: #3f78c4;
    --house: #3a3f4a;
  }
  * { margin: 0; padding: 0; box-sizing: border-box; }
  html, body { width: 1200px; height: 801px; overflow: hidden; }
  body {
    background: var(--bg);
    font-family: "Open Sans", sans-serif;
    display: flex; align-items: center; justify-content: center; gap: 36px;
  }
  .card {
    width: 560px; height: 320px; position: relative; overflow: hidden;
    background: var(--card-black);
    border: 3px solid var(--gold-edge);
  }
  /* Contact side */
  .brand { position: absolute; left: 44px; top: 104px; width: 230px; }
  .brand-name {
    color: var(--ivory); font-weight: 600; font-size: 30px; line-height: 1.1;
  }
  .brand-lines {
    margin-top: 10px; display: flex; gap: 14px;
    font-family: "Cormorant Garamond", serif; font-weight: 700;
    font-size: 19px; color: var(--gold);
  }
  .divider {
    position: absolute; left: 290px; top: 70px; width: 1px; height: 130px;
    background: var(--gold);
  }
  .contact { position: absolute; left: 316px; top: 72px; }
  .person-name { color: var(--gold); font-weight: 700; font-size: 21px; letter-spacing: 0.5px; }
  .person-role { color: var(--ivory); font-size: 15px; margin-bottom: 20px; }
  .contact-row { display: flex; align-items: center; gap: 7px; color: var(--ivory); font-size: 15px; line-height: 1.5; }
  .contact-row svg { width: 13px; height: 13px; flex: none; }
  .services {
    position: absolute; left: 0; right: 0; bottom: 34px; text-align: center;
    color: var(--ivory); font-size: 16px; letter-spacing: 0.3px;
  }
  /* Photo side */
  .photo {
    position: absolute; left: 170px; top: 0; right: 0; height: 235px;
    background:
      linear-gradient(90deg, var(--card-black) 0%, rgba(28,28,28,0.6) 30%, rgba(28,28,28,0) 60%),
      linear-gradient(180deg, var(--sky) 0%, #7fa7d6 35%, var(--house) 55%, #5d5a52 100%);
  }
  .front .brand { top: 62px; left: 40px; }
  .band {
    position: absolute; left: 0; right: 0; top: 228px; height: 62px;
    background: var(--gold); padding: 8px 26px;
    color: #1a1a1a; font-size: 17px; line-height: 1.35;
  }
</style>
</head>
<body>
  <section class="card back">
    <div class="brand">
      <div class="brand-name">Gilded<br>Slatworks</div>
      <div class="brand-lines"><span>Shutters</span><span>Shades</span><span>Blinds</span></div>
    </div>
    <div class="divider"></div>
    <div class="contact">
      <div class="person-name">DANIEL TREVICK</div>
      <div class="person-role">Owner</div>
      <div class="contact-row">
        <svg viewBox="0 0 16 16"><path fill="var(--gold)" d="M3 1h3l1.5 4-2 1.2a9 9 0 0 0 4.3 4.3L11 8.5l4 1.5v3a2 2 0 0 1-2 2A12 12 0 0 1 1 3a2 2 0 0 1 2-2z"/></svg>
        <span>919-555-0148</span>
      </div>
      <div class="contact-row">
        <svg viewBox="0 0 16 16"><circle cx="8" cy="8" r="7" fill="var(--gold)"/><path d="M1 8h14M8 1c3 3 3 11 0 14M8 1c-3 3-3 11 0 14" stroke="var(--card-black)" stroke-width="1.2" fill="none"/></svg>
        <span>gildedslatworks.com</span>
      </div>
    </div>
    <div class="services">Custom Interior &amp; Exterior Window Treatments</div>
  </section>

  <section class="card front">
    <div class="photo" role="img" aria-label="Photo of a brick home with a covered porch fitted with motorized exterior shades under a blue sky"></div>
    <div class="brand">
      <div class="brand-name">Gilded<br>Slatworks</div>
      <div class="brand-lines"><span>Shutters</span><span>Shades</span><span>Blinds</span></div>
    </div>
    <div class="band">Custom Plantation Shutters &amp;<br>Motorized Architectural Shading Systems</div>
  </section>
</body>
</html>
```